Website Design Request - Management Consulting Firm

We need a Website designed for an IT Management Staffing and Recruiting firm called TRAVENOK based in San Francisco.

The firm is an high-end technology staffing agency. Our focus is on quality and high-caliber candidates rather than quantity.

The website will have two main home pages. One for the recruiter and another on for the candidates.

The website needs to optimize for mobile devices as well.

I have attached few mock-ups that I have done just to show what I am thinking. The UI needs to be very clean, fluid, and it needs to have a modern, rustic, professional feel to it.

Target Market(s)

Technology Manager, Director, VP, CIO of Companies that have $4b-10b dollar revenue. Such as larkspurdwellings.example , https://www.velmorian.example/, quillnet.example, zib.example

Industry/Entity Type

Management Consulting

Number of Pages Required

5+ page

Font styles to use
Sans Serif

Colors
f37122
ffffff

Requirements
Must have
• Please review mock-ups for suggestions
Nice to have
Should not have

```html
<!DOCTYPE html>
<html lang="en">
<head>
<meta charset="utf-8">
<title>TRAVENOK – Hire Top IT Project Management Talents</title>
<link rel="stylesheet" href="https://fonts.googleapis.com/css2?family=Nunito+Sans:wght@300;400;600;700&display=swap">
<style>
  :root {
    --orange: #f7950f;
    --orange-deep: #f37122;
    --white: #ffffff;
    --ink: #4a4a4a;
    --ink-soft: #6b6b6b;
    --muted: #a9a9a9;
    --line: #e2e2e2;
    --panel: #f7f7f7;
    --dark-btn: #2b2b2b;
    --font: "Nunito Sans", Arial, sans-serif;
  }
  * { box-sizing: border-box; margin: 0; padding: 0; }
  html, body { width: 740px; height: 1200px; overflow: hidden; }
  body { position: relative; font-family: var(--font); background: var(--white); color: var(--ink); }
  .abs { position: absolute; }

  /* Header */
  .site-header { position: absolute; left: 0; top: 0; width: 740px; height: 67px; background: var(--white); }
  .brand { position: absolute; left: 124px; top: 23px; }
  .brand-name { display: block; font-size: 20px; font-weight: 700; letter-spacing: 1px; color: var(--orange-deep); line-height: 20px; }
  .brand-tag { display: block; font-size: 4.6px; font-weight: 600; letter-spacing: .3px; color: var(--ink); margin-top: 2px; }
  .nav-link { position: absolute; top: 30px; font-size: 9px; color: var(--ink-soft); }
  .btn-small { position: absolute; top: 28px; height: 18px; font-size: 6px; color: var(--white); display: flex; align-items: center; justify-content: center; gap: 3px; text-transform: uppercase; }
  .btn-signin { left: 518px; width: 45px; background: var(--orange); }
  .btn-signup { left: 570px; width: 46px; background: var(--dark-btn); }

  /* Hero */
  .hero { position: absolute; left: 0; top: 67px; width: 740px; height: 348px; }
  .hero-photo { position: absolute; inset: 0; background: linear-gradient(100deg, #8a8886 0%, #a9a6a2 35%, #9c9b99 60%, #7d7c7b 100%); }
  .hero-shade { position: absolute; inset: 0; background: rgba(40,40,40,.45); }
  .hero-title { position: absolute; top: 82px; width: 740px; text-align: center; font-size: 21px; font-weight: 400; color: var(--orange); }
  .hero-sub { position: absolute; top: 114px; width: 740px; text-align: center; font-size: 7.5px; color: var(--white); }
  .signup-box { position: absolute; left: 166px; top: 152px; width: 408px; height: 31px; background: var(--white); }
  .signup-box span { position: absolute; left: 12px; top: 10px; font-size: 7.5px; color: var(--muted); }
  .btn-start { position: absolute; right: 4px; top: 4px; width: 84px; height: 22px; background: var(--orange); color: var(--white); font-size: 7.5px; display: flex; align-items: center; justify-content: center; }
  .hero-terms { position: absolute; top: 197px; width: 740px; text-align: center; font-size: 7.5px; color: var(--white); }
  .hero-job { position: absolute; top: 279px; width: 740px; text-align: center; font-size: 7.5px; color: var(--white); }
  .accent { color: var(--orange); }
  .dots { position: absolute; top: 317px; left: 355px; display: flex; gap: 5px; }
  .dots i { width: 4px; height: 4px; border-radius: 50%; background: var(--white); }
  .dots i.on { background: var(--orange); }

  /* Tabs */
  .tabs { position: absolute; left: 0; top: 415px; width: 740px; height: 56px; background: var(--orange); }
  .tab { position: absolute; top: 20px; font-size: 13px; color: var(--white); transform: translateX(-50%); font-weight: 300; }
  .tab-line { position: absolute; left: 210px; top: 42px; width: 77px; height: 2px; background: var(--white); }

  /* Focus cards */
  .card { position: absolute; top: 546px; width: 157px; height: 156px; border: 1px solid var(--line); background: var(--white); text-align: center; }
  .card-icon { position: absolute; left: 52px; top: -27px; width: 53px; height: 53px; border-radius: 50%; border: 1.5px solid var(--orange); background: var(--white); display: flex; align-items: center; justify-content: center; }
  .card-title { position: absolute; top: 34px; width: 100%; font-size: 8px; color: var(--ink-soft); }
  .card-text { position: absolute; width: 100%; padding: 0 16px; font-size: 5.6px; line-height: 11px; color: var(--muted); }

  /* Hiring flexibility */
  .hiring { position: absolute; left: 0; top: 747px; width: 740px; height: 287px; background: var(--panel); }
  .hiring-title { position: absolute; top: 34px; width: 740px; text-align: center; font-size: 13px; color: var(--orange); }
  .hiring-sub { position: absolute; top: 63px; width: 740px; text-align: center; font-size: 5.6px; color: var(--muted); }
  .col-head { position: absolute; top: 104px; font-size: 10px; color: var(--ink-soft); }
  .divider { position: absolute; left: 370px; top: 103px; width: 1px; height: 154px; background: var(--line); }
  .perk { position: absolute; font-size: 6.6px; line-height: 14px; color: var(--ink-soft); }
  .perk-icon { position: absolute; width: 14px; height: 14px; }

  /* Footer */
  .site-footer { position: absolute; left: 0; top: 1034px; width: 740px; height: 134px; background: var(--white); border-top: 1px solid #ececec; }
  .foot-col { position: absolute; top: 30px; }
  .foot-col h4 { font-size: 7.5px; font-weight: 400; color: var(--orange); margin-bottom: 13px; }
  .foot-col a { display: block; font-size: 5.6px; color: var(--ink-soft); text-decoration: none; line-height: 13.8px; }
  .copyright { position: absolute; left: 0; top: 1168px; width: 740px; height: 32px; background: var(--white); border-top: 1px solid #ececec; text-align: center; font-size: 5.6px; line-height: 30px; color: var(--ink); }
</style>
</head>
<body>

<header class="site-header">
  <div class="brand">
    <span class="brand-name">TRAVENOK</span>
    <span class="brand-tag">PROJECT MANAGEMENT CONSULTING</span>
  </div>
  <span class="nav-link" style="left:390px">Professional</span>
  <span class="nav-link" style="left:460px">Employers</span>
  <span class="btn-small btn-signin">
    <svg width="6" height="6" viewBox="0 0 10 10"><path d="M1 5h6M4 2l3 3-3 3" stroke="#fff" stroke-width="1.6" fill="none"/><path d="M7 1h2v8H7" stroke="#fff" stroke-width="1.2" fill="none"/></svg>Sign In
  </span>
  <span class="btn-small btn-signup">
    <svg width="6" height="6" viewBox="0 0 10 10"><path d="M3 1H1v8h2" stroke="#fff" stroke-width="1.2" fill="none"/><path d="M3 5h6M6 2l3 3-3 3" stroke="#fff" stroke-width="1.6" fill="none"/></svg>Sign Up
  </span>
</header>

<section class="hero">
  <div class="hero-photo" role="img" aria-label="Photo of a business meeting: a presenter at a whiteboard and colleagues applauding around a conference table"></div>
  <div class="hero-shade"></div>
  <h1 class="hero-title">Hire Top IT Project Management Talents</h1>
  <p class="hero-sub">Search our networks, Shortlists candidates, send interview requests &amp; fill positions Fast</p>
  <div class="signup-box">
    <span>Your Business E-mail Address</span>
    <div class="btn-start">GET STARTED</div>
  </div>
  <p class="hero-terms">By entering your e-mail address, you agree to our <span class="accent">Terms &amp; Conditions</span></p>
  <p class="hero-job">Looking for a job &nbsp;? &nbsp;<span class="accent">Upload Resume</span> and let compnanies send you offers</p>
  <div class="dots"><i class="on"></i><i></i><i></i><i></i></div>
</section>

<nav class="tabs">
  <span class="tab" style="left:248px">Our Focus</span>
  <span class="tab" style="left:410px">Why Us ?</span>
  <span class="tab" style="left:555px">How It Works ?</span>
  <div class="tab-line"></div>
</nav>

<article class="card" style="left:123px">
  <div class="card-icon">
    <svg width="26" height="26" viewBox="0 0 26 26" fill="none" stroke="#333" stroke-width="1.1">
      <circle cx="13" cy="6" r="3"/><path d="M9 12h8v3H9z"/><path d="M13 15v3M5 18h16M5 18v2M13 18v2M21 18v2"/>
      <rect x="3" y="20" width="4" height="3"/><rect x="11" y="20" width="4" height="3"/><rect x="19" y="20" width="4" height="3"/>
    </svg>
  </div>
  <h3 class="card-title">Project Managers</h3>
  <p class="card-text" style="top:54px">Manage IT Projects, Programs and Portfolio from start to finish</p>
  <p class="card-text" style="top:86px">Get your projects back on track with our highly vetted consultants</p>
  <p class="card-text" style="top:116px">Conduct Project audits,lessons learned and post-mortem</p>
</article>

<article class="card" style="left:292px">
  <div class="card-icon">
    <svg width="26" height="26" viewBox="0 0 26 26" fill="none" stroke="#333" stroke-width="1.1">
      <rect x="3" y="8" width="20" height="13" rx="1"/><path d="M10 8V5h6v3M3 13h20"/><rect x="7" y="12" width="2" height="3"/><rect x="17" y="12" width="2" height="3"/>
    </svg>
  </div>
  <h3 class="card-title">PMO Leadership</h3>
  <p class="card-text" style="top:54px">Manage IT Projects, Programs and Portfolio from start to finish</p>
  <p class="card-text" style="top:86px">Get your projects back on track with our highly vetted consultants</p>
  <p class="card-text" style="top:116px">Conduct Project audits,lessons learned and post-mortem</p>
</article>

<article class="card" style="left:461px">
  <div class="card-icon">
    <svg width="26" height="26" viewBox="0 0 26 26" fill="none" stroke="#333" stroke-width="1.1">
      <rect x="3" y="5" width="20" height="14"/><path d="M13 3v2M9 24l4-5 4 5"/><path d="M6 16l4-4 3 2 6-6M16 8h3v3"/>
    </svg>
  </div>
  <h3 class="card-title">PM Trainer &amp; Coaches</h3>
  <p class="card-text" style="top:54px">Manage IT Projects, Programs and Portfolio from start to finish</p>
  <p class="card-text" style="top:86px">Get your projects back on track with our highly vetted consultants</p>
  <p class="card-text" style="top:116px">Conduct Project audits,lessons learned and post-mortem</p>
</article>

<section class="hiring">
  <h2 class="hiring-title">Hiring Flexibility</h2>
  <p class="hiring-sub">Hire an hourly basis or bring them on as permanent employees</p>
  <h3 class="col-head" style="left:123px">Contract Rates</h3>
  <h3 class="col-head" style="left:395px">Permanent Roles</h3>
  <div class="divider"></div>

  <svg class="perk-icon" style="left:124px;top:140px" viewBox="0 0 14 14" fill="none" stroke="#f7950f" stroke-width="1.6"><circle cx="7" cy="7" r="5.5"/><path d="M7 4v3.5h-2.5"/></svg>
  <p class="perk" style="left:152px;top:139px">Flexible hourlyrate ideal for contract,Part-timeor<br>interim positionsstructure as needed</p>
  <svg class="perk-icon" style="left:124px;top:184px" viewBox="0 0 14 14" fill="none" stroke="#f7950f" stroke-width="2"><circle cx="6" cy="6" r="4"/><path d="M9 9l4 4"/></svg>
  <p class="perk" style="left:152px;top:184px">Search our datatbase and schedule interviews directly</p>
  <svg class="perk-icon" style="left:124px;top:225px" viewBox="0 0 14 14" fill="#f7950f"><circle cx="7" cy="4" r="3"/><path d="M1 13c0-4 3-5.5 6-5.5s6 1.5 6 5.5z"/></svg>
  <p class="perk" style="left:152px;top:225px">25% Cheaper than traditional staffing firms</p>

  <svg class="perk-icon" style="left:396px;top:141px" viewBox="0 0 14 14"><circle cx="7" cy="7" r="6" fill="#f7950f"/><path d="M4 5c2 0 2 2 4 1s1 3 3 2" stroke="#fff" stroke-width="1.2" fill="none"/></svg>
  <p class="perk" style="left:422px;top:139px">National Reach-Find the Best candidate int he nation</p>
  <svg class="perk-icon" style="left:395px;top:184px" viewBox="0 0 14 14" fill="none" stroke="#f7950f" stroke-width="1.5"><rect x="1" y="3.5" width="12" height="7"/><circle cx="7" cy="7" r="1.8" fill="#f7950f"/></svg>
  <p class="perk" style="left:422px;top:184px">50% cheaper than traditonal recruiting fees</p>
  <svg class="perk-icon" style="left:396px;top:224px" viewBox="0 0 14 14" fill="none" stroke="#f7950f" stroke-width="1.4"><path d="M1 6h3v7H1zM4 12h6.5l1.5-5H8l.5-4c-1 0-2 1-2.5 3L4 7"/></svg>
  <p class="perk" style="left:422px;top:225px">White glove services for all permanant rates</p>
</section>

<footer class="site-footer">
  <div class="brand" style="top:30px">
    <span class="brand-name">TRAVENOK</span>
    <span class="brand-tag">PROJECT MANAGEMENT CONSULTING</span>
  </div>
  <div class="foot-col" style="left:286px">
    <h4>Job Seekers</h4>
    <a href="#">How It Works</a><a href="#">Browse Jobs</a><a href="#">Create Profile</a>
  </div>
  <div class="foot-col" style="left:392px">
    <h4>Clients</h4>
    <a href="#">How It Works</a><a href="#">Browse Resumes</a><a href="#">Post Jobs for Free</a><a href="#">Sign Up</a>
  </div>
  <div class="foot-col" style="left:494px">
    <h4>Services</h4>
    <a href="#">Staffing</a><a href="#">Direct Hire</a>
  </div>
  <div class="foot-col" style="left:578px">
    <h4>About Us</h4>
    <a href="#">Our Mission</a><a href="#">Our Vision</a><a href="#">Our Values</a>
  </div>
</footer>
<div class="copyright">© 2016 Company Name &nbsp;|&nbsp; All Rights Reserved</div>

</body>
</html>
```